Business Card for Professional Domainer

Require a business card design for an Individual Person who is a Professional Domainer.

Who is a Professional Domainer?
A domainer is someone who earns a profit buying and selling domain names.
Professional Domainer are the ones who do this on a full time basis.

So we require the business card design to be related to the above work.

There is no company or any logo currently, as the card is required for an Individual Person.

Business Card required to mention following details:

1. Full Name of the Person (Ex: Marisol Pike)
2. Education Qualification (Ex: B.Tech Computer Science)
3. Mobile Number (Ex: +71 4837062915)
4. Website (Ex: www.brivolta.example)
5. Email (Ex: contact@brivolta.example)

Positioning of the details:

1. Mobile Number should be placed to Right Top Corner
2. Education Qualification should be just below Full Name
3. Website and Email should be on Bottom Part, on a bar at the bottom

It's important to include images related to the nature of work (Domaining) in the card design.
A good related image would be great. Image should be either in background or as a logo.
The image should be focus of the business card, and shoudl speak out on itself.
Anyone looking at the card should understand at one look what work is being done.
So kindly use images in the design which are highly relevant to domaining and domain names.

Along with the image, it's also good if you use the word "Professional Domainer" anywhere in the design.
Maybe along with the image or somewhere it would fit. These words would be like company name.
So please try to use these words "Professional Domainer" in the design, as it will help a lot.

Colors: Blue, Red, Green

We like these colors, but you are free to use any color which would be good for the design.

Card design should be according to PressaLine specs:

Document Trim Size = 91 x 55 mm | 1075 x 650 pixels
Full Bleed Size = 94 x 58 mm | 1110 x 685 pixels

Last thing, the business card should look professional and clean.
People should know that the person is a Professional Domainer at one look of the card.

Thank You and All the Best :)

Message to the the designers working on this project:

We have now guaranteed this project. This means, we will 100% choose a design and award the project to the one we like the best. So kindly submit your best designs before Wednesday, 3 July 2013. After that we are going to finalize the project and award to the best one. So please hurry up so that you are not too late. Thank You and All the Best!

```html
<!DOCTYPE html>
<html lang="en">
<head>
<meta charset="utf-8">
<title>Marisol Pike – Professional Domainer</title>
<link rel="stylesheet" href="https://fonts.googleapis.com/css2?family=Montserrat:wght@800&family=Questrial&display=swap">
<style>
  :root {
    --ink-dark: #0b0f12;
    --suit: #15191c;
    --shirt: #d9dcdc;
    --teal-deep: #0f3d4c;
    --teal: #1e6f86;
    --teal-light: #4aaec6;
    --glow: #bfe6ef;
    --steel: #4d8197;
    --frame: #4a7f96;
    --white: #ffffff;
    --pale: #e6e9ea;
    --charcoal: #2f3a40;
  }
  html, body {
    margin: 0;
    padding: 0;
    width: 1200px;
    height: 741px;
    overflow: hidden;
    background: #ffffff;
  }
  .card {
    position: relative;
    width: 1200px;
    height: 741px;
    overflow: hidden;
    font-family: "Questrial", sans-serif;
  }
  .photo-area {
    position: absolute;
    inset: 0;
    background:
      radial-gradient(circle 60px at 750px 158px, var(--glow) 0%, rgba(191,230,239,0.35) 40%, rgba(191,230,239,0) 100%),
      radial-gradient(ellipse 180px 130px at 720px 380px, rgba(214,170,150,0.55) 0%, rgba(214,170,150,0) 100%),
      radial-gradient(ellipse 560px 440px at 830px 170px, var(--teal-light) 0%, rgba(74,174,198,0) 72%),
      radial-gradient(ellipse 130px 420px at 100px 330px, var(--shirt) 0%, rgba(217,220,220,0.6) 55%, rgba(217,220,220,0) 100%),
      linear-gradient(100deg, var(--ink-dark) 0%, var(--suit) 36%, #1a2a30 48%, var(--teal-deep) 58%, var(--teal) 82%, #14566a 100%);
  }
  .shapes {
    position: absolute;
    inset: 0;
  }
  .rotated {
    position: absolute;
    white-space: nowrap;
    line-height: 1;
  }
  .tagline {
    color: var(--pale);
    font-size: 90px;
    letter-spacing: 1px;
    transform-origin: left bottom;
    transform: rotate(20deg);
  }
  .tagline--first { left: 570px; top: 86px; }
  .tagline--second { left: 598px; top: 207px; }
  .holder-name {
    left: 382px;
    top: 364px;
    font-family: "Montserrat", sans-serif;
    font-weight: 800;
    font-size: 74px;
    letter-spacing: 8px;
    color: var(--white);
    transform-origin: left bottom;
    transform: rotate(20deg);
  }
  .qualification {
    left: 368px;
    top: 456px;
    font-size: 38px;
    letter-spacing: 1px;
    color: var(--white);
    transform-origin: left bottom;
    transform: rotate(19deg);
  }
  .contact {
    transform-origin: left bottom;
    transform: rotate(-72deg);
  }
  .contact--web {
    left: 96px;
    top: 510px;
    font-family: "Montserrat", sans-serif;
    font-weight: 800;
    font-size: 28px;
    color: var(--white);
  }
  .contact--mail {
    left: 144px;
    top: 548px;
    font-family: "Montserrat", sans-serif;
    font-weight: 800;
    font-size: 26px;
    color: var(--charcoal);
  }
  .contact--phone {
    left: 230px;
    top: 640px;
    font-size: 48px;
    color: var(--white);
  }
</style>
</head>
<body>
  <div class="card">
    <div class="photo-area" role="img" aria-label="Photograph of a person in a dark suit touching a glowing network of connected domain nodes on a teal background"></div>

    <svg class="shapes" width="1200" height="741" viewBox="0 0 1200 741" aria-hidden="true">
      <polygon class="contact-bar" points="232,186 416,242 250,770 60,770" fill="var(--steel)"/>
      <polyline class="title-frame" points="528,-30 410,355 1072,578 1230,90" fill="none" stroke="var(--frame)" stroke-width="14"/>
    </svg>

    <div class="rotated tagline tagline--first">Professional</div>
    <div class="rotated tagline tagline--second">Domainer</div>

    <div class="rotated holder-name">Marisol Pike</div>
    <div class="rotated qualification">B.Tech Computer Science</div>

    <div class="rotated contact contact--web">www.brivolta.example</div>
    <div class="rotated contact contact--mail">contact@brivolta.example</div>
    <div class="rotated contact contact--phone">Ph:&nbsp; +71 4837062915</div>
  </div>
</body>
</html>
```